Business Card Design Project

I need a business card designed from scratch. I have an existing logo that I can upload in Illustrator for modification or redesign.

The Company is called Query Lanterns http://querylanterns.com.au and we provide Search Engine Optimization services to Australian businesses. The current logo signifies an increase in visitors, profits etc...

There are no restrictions as to the redesign - colours, style etc are all open to change.

Cards will be full colour and one sided printed at http://www.cardmoxel.com.au so check their requirements for file format and sizes etc.

I will expect all original files upon completion of project.

Target Market(s)

Any business with a web site looking to improve their search engine rankings

Industry/Entity Type

Business

Requirements
Must have
• I like modern, sleek designs. Clean, not fussy, uncluttered.

```html
<!DOCTYPE html>
<html lang="en">
<head>
<meta charset="utf-8">
<title>Query Lanterns – Business Card</title>
<link href="https://fonts.googleapis.com/css2?family=Open+Sans:wght@400;700;800&display=swap" rel="stylesheet">
<style>
  :root {
    --brand-blue: #1f6fb8;
    --brand-blue-soft: #d3e0ee;
    --brand-yellow: #f4c21a;
    --brand-yellow-soft: #fbf0c4;
    --card-white: #ffffff;
    --backdrop: #3b3b3b;
  }
  html, body {
    margin: 0;
    padding: 0;
    width: 1187px;
    height: 1200px;
    overflow: hidden;
    background: var(--backdrop);
    font-family: "Open Sans", Arial, sans-serif;
  }
  .canvas {
    position: relative;
    width: 1187px;
    height: 1200px;
  }
  .card {
    position: absolute;
    left: 220px;
    width: 727px;
    height: 471px;
    background: var(--card-white);
    overflow: hidden;
  }
  .card--front { top: 73px; }
  .card--back { top: 640px; }

  .front-mark {
    position: absolute;
    left: 180px;
    top: 40px;
    width: 387px;
    height: 360px;
    border-radius: 40px;
    background: linear-gradient(135deg, var(--brand-yellow) 0%, #9fb36a 50%, var(--brand-blue) 100%);
    opacity: 0.85;
  }

  .back-watermark {
    position: absolute;
    inset: 0;
    background: linear-gradient(60deg, var(--brand-yellow-soft) 0%, #f6f5ef 45%, var(--brand-blue-soft) 100%);
    opacity: 0.7;
  }

  .brand {
    position: absolute;
    left: 27px;
    top: 338px;
    display: flex;
    align-items: center;
    gap: 10px;
  }
  .brand__dot {
    width: 18px;
    height: 18px;
    border-radius: 50%;
    background: var(--brand-yellow);
  }
  .brand__name {
    font-size: 27px;
    font-weight: 800;
    line-height: 1.2;
    color: var(--brand-blue);
    letter-spacing: -0.5px;
    white-space: nowrap;
  }

  .divider {
    position: absolute;
    left: 321px;
    top: 300px;
    width: 4px;
    height: 127px;
    background: var(--brand-yellow);
  }

  .contact {
    position: absolute;
    left: 358px;
    top: 298px;
  }
  .contact__name {
    margin: 0 0 0 28px;
    font-size: 20px;
    font-weight: 700;
    line-height: 1.3;
    color: var(--brand-blue);
  }
  .contact__role {
    margin: 0 0 12px 32px;
    font-size: 16px;
    font-weight: 700;
    line-height: 1.3;
    color: var(--brand-blue);
    white-space: nowrap;
  }
  .contact__list {
    list-style: none;
    margin: 0;
    padding: 0;
  }
  .contact__item {
    display: flex;
    align-items: center;
    gap: 8px;
    height: 27px;
    font-size: 13px;
    font-weight: 700;
    color: var(--brand-yellow);
    white-space: nowrap;
  }
  .contact__icon {
    width: 22px;
    height: 22px;
    flex: none;
  }
</style>
</head>
<body>
<main class="canvas">

  <section class="card card--front" aria-label="Card front">
    <div class="front-mark" role="img" aria-label="Query Lanterns brand symbol: rising ribbon with upward arrows in yellow and blue"></div>
  </section>

  <section class="card card--back" aria-label="Card back">
    <div class="back-watermark" role="img" aria-label="Faint large brand symbol decoration in pale yellow and blue"></div>

    <div class="brand">
      <span class="brand__dot"></span>
      <span class="brand__name">Query Lanterns</span>
    </div>

    <div class="divider"></div>

    <div class="contact">
      <p class="contact__name">Liam Harker</p>
      <p class="contact__role">Internet Marketing Consultant</p>
      <ul class="contact__list">
        <li class="contact__item">
          <svg class="contact__icon" viewBox="0 0 22 22" aria-hidden="true">
            <circle cx="11" cy="11" r="9" fill="none" stroke="#1f6fb8" stroke-width="2"/>
            <ellipse cx="11" cy="11" rx="4" ry="9" fill="none" stroke="#1f6fb8" stroke-width="1.5"/>
            <line x1="2" y1="11" x2="20" y2="11" stroke="#1f6fb8" stroke-width="1.5"/>
          </svg>
          www.querylanterns.com.au
        </li>
        <li class="contact__item">
          <svg class="contact__icon" viewBox="0 0 22 22" aria-hidden="true">
            <rect x="2" y="5" width="18" height="12" rx="1" fill="#1f6fb8"/>
            <polyline points="2,5 11,12 20,5" fill="none" stroke="#ffffff" stroke-width="1.5"/>
          </svg>
          liam@querylanterns.com.au
        </li>
        <li class="contact__item">
          <svg class="contact__icon" viewBox="0 0 22 22" aria-hidden="true">
            <path d="M3 8 Q11 2 19 8 L17 11 L14 9 L14 7 Q11 6 8 7 L8 9 L5 11 Z" fill="#1f6fb8"/>
            <rect x="5" y="12" width="12" height="7" rx="1.5" fill="#1f6fb8"/>
          </svg>
          1300 482915
        </li>
      </ul>
    </div>
  </section>

</main>
</body>
</html>
```